Holistic/ Sports Psychologist needs flyer design

I need a flyer designed that catches the attention of potential customers - (parents of young athletes and athletes) who may be looking for psychological services. I have a logo and all the relevant info for the flyer but would like someone to take it and make it look creative, fun, fresh and attention getting for high school and college athletes. The colors used can be from my logo design which represents my holistic approach.
Target Market(s)
high school and collegiate athletes
Industry/Entity Type
sports psychology
Requirements
Must have
- Info I put on the flyer with my logo and please add some graphics and color based on my logo

```html
<!DOCTYPE html>
<html lang="en">
<head>
<meta charset="UTF-8">
<title>Holistic and Sports Psychology Consulting Flyer</title>
<link href="https://fonts.googleapis.com/css2?family=Delius&family=Poppins:wght@400;500;600;700&display=swap" rel="stylesheet">
<style>
:root{
  --navy:#143f6b;
  --blue:#2d5d9a;
  --green:#a7d174;
  --sage:#6b9b78;
  --leaf:#5e8b2f;
  --purple:#5a4aa5;
  --ink:#222a33;
  --grey:#4a4f57;
  --white:#ffffff;
}
*{margin:0;padding:0;box-sizing:border-box}
html,body{width:960px;height:1200px;overflow:hidden;background:var(--white)}
.flyer{position:relative;width:960px;height:1200px;background:var(--white);font-family:"Poppins",sans-serif;color:var(--ink)}
.brand{position:absolute;left:68px;top:50px;display:flex;align-items:center}
.brand-dot{width:92px;height:92px;border-radius:50%;border:4px solid var(--blue);background:#eef4fa}
.brand-name{position:absolute;left:100px;top:22px;font-family:"Delius",cursive;font-size:24px;color:var(--blue);white-space:nowrap}
.brand-bar{position:absolute;left:296px;top:103px;width:293px;height:19px;background:var(--green)}
.hero{position:absolute;left:0;top:151px;width:960px;height:289px;background:linear-gradient(90deg,var(--navy) 0%,#1d4f78 50%,var(--sage) 100%)}
.hero-title{position:absolute;left:70px;top:176px;font-family:"Delius",cursive;font-size:50px;line-height:56px;color:var(--white)}
.hero-title .accent{color:var(--green)}
.hero-photo{position:absolute;left:532px;top:62px;width:394px;height:384px}
.section-title{position:absolute;left:70px;top:488px;width:820px;font-weight:700;font-size:25px;line-height:31px;color:var(--blue)}
.services{position:absolute;left:40px;top:572px;width:890px;height:260px;display:flex}
.service{position:relative;text-align:center;padding:0 6px}
.service + .service::before{content:"";position:absolute;left:0;top:0;height:225px;border-left:1.5px dotted #8a8f96}
.service-icon{display:block;margin:0 auto 6px;width:70px;height:70px}
.service-name{font-weight:600;font-size:19px;line-height:22px;color:var(--purple);margin-bottom:4px}
.service-text{font-size:12.3px;line-height:15px;color:var(--ink)}
.divider{position:absolute;left:0;top:843px;width:960px;border-top:1px solid #d8dde3}
.portrait{position:absolute;left:44px;top:887px;width:210px;height:210px}
.doctor-name{position:absolute;left:276px;top:858px;font-family:"Delius",cursive;font-size:38px;color:var(--leaf)}
.bio{position:absolute;left:276px;top:910px;width:600px;font-size:10.8px;line-height:15px;color:var(--grey);letter-spacing:.2px}
.bio p + p{margin-top:14px}
.bio .label{color:var(--purple)}
.bio .specialties{color:var(--ink)}
.fact{position:absolute;top:1046px;display:flex;align-items:center;gap:16px}
.fact-text{font-weight:600;font-size:16px;line-height:20px;color:var(--ink)}
.fact-text .hl{color:var(--purple)}
.fact-online{left:279px}
.fact-sessions{left:608px}
.footer{position:absolute;left:0;top:1121px;width:960px;height:79px;background:var(--green);display:flex;align-items:center}
.contact{display:flex;align-items:center;gap:10px;font-weight:500;color:var(--ink)}
.contact + .contact{border-left:1px solid #e9f3dc}
.contact-phone{padding-left:66px;padding-right:24px;font-size:24px;font-weight:600;height:44px}
.contact-address{padding:0 28px 0 24px;font-size:15px;line-height:19px;height:44px}
.contact-web{padding-left:16px;font-size:16px;height:44px}
.contact-icon{width:24px;height:24px;flex:none}
</style>
</head>
<body>
<div class="flyer">
  <div class="brand">
    <div class="brand-dot"></div>
    <span class="brand-name">Dr. Elena Whitford</span>
  </div>
  <div class="brand-bar"></div>

  <div class="hero"></div>
  <h1 class="hero-title">Holistic<br>Psychology and<br><span class="accent">Sports Psychology<br>Consulting</span></h1>
  <svg class="hero-photo" viewBox="0 0 394 384" role="img" aria-label="Collage of sports gear on grass, a runner by the sea and cheering young athletes">
    <defs>
      <linearGradient id="collage" x1="0" y1="0" x2="1" y2="1">
        <stop offset="0" stop-color="#4d8f35"/>
        <stop offset=".5" stop-color="#9cc2d8"/>
        <stop offset="1" stop-color="#d9c9a4"/>
      </linearGradient>
    </defs>
    <circle cx="197" cy="192" r="188" fill="var(--white)" stroke="var(--blue)" stroke-width="6"/>
    <circle cx="197" cy="192" r="176" fill="url(#collage)"/>
  </svg>

  <h2 class="section-title">Ways to Improve Athletic Performance Using Sports and Holistic Psychology</h2>

  <div class="services">
    <div class="service" style="width:170px">
      <svg class="service-icon" viewBox="0 0 70 70" aria-hidden="true"><circle cx="35" cy="35" r="32" fill="var(--blue)" stroke="var(--green)" stroke-width="4"/><circle cx="35" cy="32" r="12" fill="none" stroke="#fff" stroke-width="2"/><path d="M30 46h10M31 50h8" stroke="#fff" stroke-width="2"/></svg>
      <div class="service-name">Mental<br>Skills<br>Training</div>
      <p class="service-text">Ex: visualization,<br>goal-setting,<br>motivation,<br>self- talk, mindset,<br>concentration<br>techniques</p>
    </div>
    <div class="service" style="width:185px">
      <svg class="service-icon" viewBox="0 0 70 70" aria-hidden="true"><circle cx="35" cy="35" r="32" fill="var(--blue)" stroke="var(--green)" stroke-width="4"/><path d="M24 48V38a12 12 0 1 1 22 0l-4 10z" fill="none" stroke="#fff" stroke-width="2"/></svg>
      <div class="service-name">Performance<br>Enhancement</div>
      <p class="service-text">Eliminate<br>psychological<br>barriers that are<br>hindering performance<br>such as self- doubt,<br>perfectionism, fear<br>of failure, and burnout</p>
    </div>
    <div class="service" style="width:142px">
      <svg class="service-icon" viewBox="0 0 70 70" aria-hidden="true"><circle cx="35" cy="35" r="32" fill="var(--blue)" stroke="var(--green)" stroke-width="4"/><circle cx="35" cy="30" r="9" fill="none" stroke="#fff" stroke-width="2"/><path d="M18 36l8 14M52 36l-8 14" stroke="#fff" stroke-width="2"/></svg>
      <div class="service-name">Mental<br>Health</div>
      <p class="service-text">Anxiety and stress<br>management by<br>using things such<br>as relaxation<br>techniques,<br>breathwork, and<br>mindfulness<br>practices</p>
    </div>
    <div class="service" style="width:212px">
      <svg class="service-icon" viewBox="0 0 70 70" aria-hidden="true"><circle cx="35" cy="35" r="32" fill="var(--blue)" stroke="var(--green)" stroke-width="4"/><path d="M25 50V36a10 10 0 1 1 20 0v4l-3 10z" fill="none" stroke="#fff" stroke-width="2"/><circle cx="36" cy="33" r="4" fill="none" stroke="#fff" stroke-width="2"/></svg>
      <div class="service-name">Injury Recovery<br>Support</div>
      <p class="service-text">Assist athletes in<br>maintain resilience and<br>positive mental attitude<br>during rehabilitation as well<br>as processing emotions<br>relating to any potential<br>trauma caused by the<br>injury or life transitions<br>resulting from it.</p>
    </div>
    <div class="service" style="width:176px">
      <svg class="service-icon" viewBox="0 0 70 70" aria-hidden="true"><circle cx="35" cy="35" r="32" fill="var(--blue)" stroke="var(--green)" stroke-width="4"/><circle cx="35" cy="24" r="5" fill="none" stroke="#fff" stroke-width="2"/><path d="M35 30v12M24 48h22M28 36l7 6 7-6" fill="none" stroke="#fff" stroke-width="2"/></svg>
      <div class="service-name">Burnout<br>prevention</div>
      <p class="service-text">Teach athletes how<br>to have balance in<br>sports and life so<br>they can experience<br>longevity in their<br>sports as well<br>asoverall optimal<br>health and<br>well-being.</p>
    </div>
  </div>

  <div class="divider"></div>

  <svg class="portrait" viewBox="0 0 210 210" role="img" aria-label="Portrait photo of the psychologist seated on a rocky shoreline">
    <defs>
      <linearGradient id="portraitFill" x1="0" y1="0" x2="0" y2="1">
        <stop offset="0" stop-color="#9fb0bf"/>
        <stop offset="1" stop-color="#3b4f7a"/>
      </linearGradient>
    </defs>
    <circle cx="105" cy="105" r="101" fill="url(#portraitFill)" stroke="var(--blue)" stroke-width="4"/>
  </svg>

  <h2 class="doctor-name">Dr. Elena Whitford</h2>
  <div class="bio">
    <p>Dr. Elena Whitford is a licensed psychologist. She understands the unique experiences of athletes due to her background as an All- American swimmer, collegiate and age group swim coach, parent of a collegiate/professional athlete, and sports psychology researcher. She works with athletes to optimize performance and overall well-being.</p>
    <p class="specialties"><span class="label">Her specializations include:</span> performance anxiety, mental performance,Stress management, anxiety, depressions, trauma, life transitions,relationship issues, injury, and sleep.</p>
  </div>

  <div class="fact fact-online">
    <p class="fact-text">All services are provided<br><span class="hl">online via telehealth.</span></p>
    <svg width="42" height="42" viewBox="0 0 42 42" aria-hidden="true"><rect x="3" y="8" width="36" height="24" rx="2" fill="none" stroke="var(--blue)" stroke-width="2"/><path d="M15 38h12M21 32v6" stroke="var(--blue)" stroke-width="2"/><circle cx="21" cy="17" r="4" fill="none" stroke="var(--blue)" stroke-width="2"/><path d="M14 28a7 6 0 0 1 14 0" fill="none" stroke="var(--blue)" stroke-width="2"/></svg>
  </div>
  <div class="fact fact-sessions">
    <p class="fact-text">Sessions are<br><span class="hl">30 or 55 minutes.</span></p>
    <svg width="40" height="40" viewBox="0 0 40 40" aria-hidden="true"><circle cx="20" cy="20" r="17" fill="none" stroke="var(--blue)" stroke-width="2"/><path d="M20 9v11l7 6" fill="none" stroke="var(--blue)" stroke-width="2"/></svg>
  </div>

  <footer class="footer">
    <div class="contact contact-phone">
      <svg class="contact-icon" viewBox="0 0 24 24" aria-hidden="true"><circle cx="12" cy="12" r="12" fill="var(--purple)"/><path d="M8 6l2 3-1.5 1.5a7 7 0 0 0 5 5L15 14l3 2-1 2c-5 0-10-5-10-10z" fill="#fff"/></svg>
      <span>555-017-2290</span>
    </div>
    <div class="contact contact-address">
      <svg class="contact-icon" viewBox="0 0 24 24" aria-hidden="true"><circle cx="12" cy="12" r="12" fill="var(--purple)"/><path d="M12 5a4 4 0 0 1 4 4c0 3-4 8-4 8s-4-5-4-8a4 4 0 0 1 4-4z" fill="#fff"/><circle cx="12" cy="9" r="1.5" fill="var(--purple)"/></svg>
      <span>880 Harbor Lane #14<br>Bayview Shores, FL 32999</span>
    </div>
    <div class="contact contact-web">
      <svg class="contact-icon" viewBox="0 0 24 24" aria-hidden="true"><circle cx="12" cy="12" r="12" fill="var(--purple)"/><circle cx="12" cy="12" r="6" fill="none" stroke="#fff" stroke-width="1.4"/><path d="M6 12h12M12 6c-3 3-3 9 0 12M12 6c3 3 3 9 0 12" fill="none" stroke="#fff" stroke-width="1.2"/></svg>
      <span>www.drelenawhitford.com</span>
    </div>
  </footer>
</div>
</body>
</html>
```